RTavenor Business Cards & Letterhead

I have a logo but need a design for some new business cards. We are a Design-Build Firm that specializes in the design and construction of commercial projects.
the cards need to be professional. no cartoon stuff.
i would like to have the cards in AI format so I can update the card as needed. Logo is provided.
Our Address is: 4187 Marlowe Ct. Apex, North Carolina 27614

```html
<!DOCTYPE html>
<html lang="en">
<head>
<meta charset="utf-8">
<title>RTavenor Business Card</title>
<link rel="stylesheet" href="https://fonts.googleapis.com/css2?family=Open+Sans:wght@400;600;700;800&display=swap">
<style>
  :root {
    --stage: #333335;
    --card: #1f1f23;
    --wordmark: #76777b;
    --accent: #1b7fc6;
    --accent-deep: #125a94;
    --ink: #ffffff;
    --shadow: rgba(0, 0, 0, 0.55);
  }
  * { box-sizing: border-box; margin: 0; padding: 0; }
  html, body {
    width: 1200px;
    height: 780px;
    overflow: hidden;
    background: var(--stage);
    font-family: "Open Sans", Arial, sans-serif;
  }
  .sheet {
    position: relative;
    width: 1200px;
    height: 780px;
  }
  .card {
    position: absolute;
    top: 235px;
    width: 540px;
    height: 309px;
    background: var(--card);
    box-shadow: 0 10px 24px var(--shadow);
    overflow: hidden;
  }
  .card--back { left: 45px; }
  .card--front { left: 615px; }

  /* Wordmark */
  .wordmark {
    display: flex;
    align-items: center;
    gap: 10px;
    color: var(--wordmark);
    font-weight: 800;
    letter-spacing: 0.02em;
    line-height: 1;
  }
  .wordmark__square {
    background: var(--accent);
    flex: none;
  }
  .card--back .wordmark {
    position: absolute;
    left: 50%;
    top: 50%;
    transform: translate(-50%, -50%);
    font-size: 56px;
    gap: 16px;
  }
  .card--back .wordmark__square { width: 40px; height: 40px; }

  .card--front .wordmark {
    position: absolute;
    left: 34px;
    top: 42px;
    font-size: 34px;
  }
  .card--front .wordmark__square { width: 24px; height: 24px; }
  .wordmark__reg {
    font-size: 11px;
    font-weight: 600;
    align-self: flex-start;
    margin-left: -6px;
  }

  /* Name block */
  .identity {
    position: absolute;
    right: 0;
    top: 86px;
    display: flex;
    align-items: stretch;
    gap: 10px;
  }
  .identity__text { text-align: right; padding-top: 2px; }
  .identity__name {
    color: var(--accent);
    font-weight: 700;
    font-size: 24px;
    letter-spacing: 0.03em;
    line-height: 1.05;
  }
  .identity__role {
    color: var(--ink);
    font-weight: 600;
    font-size: 14px;
    letter-spacing: 0.02em;
    margin-top: 4px;
  }
  .identity__bar {
    width: 16px;
    background: linear-gradient(90deg, var(--accent-deep), var(--accent));
  }

  /* Address */
  .address {
    position: absolute;
    left: 40px;
    top: 158px;
    color: var(--ink);
    font-size: 14px;
    line-height: 1.35;
    font-style: normal;
  }

  /* Contacts */
  .contacts {
    position: absolute;
    left: 40px;
    bottom: 24px;
    list-style: none;
    color: var(--ink);
    font-size: 14px;
    line-height: 1.35;
  }
  .contacts__item {
    display: flex;
    align-items: center;
    gap: 9px;
  }
  .contacts__icon {
    width: 13px;
    height: 13px;
    flex: none;
  }
</style>
</head>
<body>
<main class="sheet">

  <section class="card card--back" aria-label="Card back">
    <div class="wordmark">
      <span class="wordmark__square"></span>
      <span class="wordmark__name">RTAVENOR</span>
      <span class="wordmark__reg">®</span>
    </div>
  </section>

  <section class="card card--front" aria-label="Card front">
    <div class="wordmark">
      <span class="wordmark__square"></span>
      <span class="wordmark__name">RTAVENOR</span>
      <span class="wordmark__reg">®</span>
    </div>

    <div class="identity">
      <div class="identity__text">
        <p class="identity__name">RAYMOND TAVENOR</p>
        <p class="identity__role">Founder/President</p>
      </div>
      <span class="identity__bar"></span>
    </div>

    <address class="address">
      4187 Marlowe Ct. Apex,<br>
      North Carolina 27614
    </address>

    <ul class="contacts">
      <li class="contacts__item">
        <svg class="contacts__icon" viewBox="0 0 16 16" aria-hidden="true">
          <path fill="#1b7fc6" d="M3.6 1.5l2.3 2.6-1.3 1.7c.9 2 2.6 3.7 4.6 4.6l1.7-1.3 2.6 2.3-1.2 2.6C6.9 13.8 2.2 9.1 1 3.7z"/>
        </svg>
        <span>(919) 555-0142</span>
      </li>
      <li class="contacts__item">
        <svg class="contacts__icon" viewBox="0 0 16 16" aria-hidden="true">
          <g fill="none" stroke="#1b7fc6" stroke-width="1.5">
            <circle cx="8" cy="8" r="6.5"/>
            <ellipse cx="8" cy="8" rx="2.8" ry="6.5"/>
            <path d="M1.5 8h13"/>
          </g>
        </svg>
        <span>www.rtavenor.com</span>
      </li>
      <li class="contacts__item">
        <svg class="contacts__icon" viewBox="0 0 16 16" aria-hidden="true">
          <rect x="1" y="3.5" width="14" height="9" rx="1" fill="#1b7fc6"/>
          <path d="M1.5 4.2L8 9l6.5-4.8" fill="none" stroke="#1f1f23" stroke-width="1.3"/>
        </svg>
        <span>RMT@RTavenor.com</span>
      </li>
    </ul>
  </section>

</main>
</body>
</html>
```